business card deign

Logo needs the following on it.
1. attached logo
2. Tagline - "If it keeps a drink cold or the party going...we do it!"
3. Name- Dalton Pikes, Founder and CPO
4. Address - 412 E. Carver Avenue, Ste 2207, Tampa, FL. 33917
5. Phone - 555.318.4726

```html
<!DOCTYPE html>
<html lang="en">
<head>
<meta charset="utf-8">
<title>Kelvara Business Card</title>
<link href="https://fonts.googleapis.com/css2?family=Montserrat:wght@400;500;700&display=swap" rel="stylesheet">
<style>
  :root {
    --stage: #3a3a3a;
    --ink: #111111;
    --paper: #ffffff;
    --band: #151515;
    --swoosh: #8c8c8c;
    --pattern-light: #d9d9d9;
    --pattern-dark: #0c0c0c;
  }
  * { margin: 0; padding: 0; box-sizing: border-box; }
  html, body { width: 1200px; height: 689px; overflow: hidden; }
  body {
    background: var(--stage);
    font-family: "Montserrat", Arial, sans-serif;
    display: flex;
    align-items: center;
    justify-content: center;
    gap: 40px;
  }
  .card {
    position: relative;
    width: 560px;
    height: 320px;
    border-radius: 22px;
    overflow: hidden;
  }
  /* Back side */
  .card-back { background: var(--pattern-dark); }
  .back-pattern {
    position: absolute; inset: 0;
    background: linear-gradient(120deg, var(--pattern-light) 0%, #6e6e6e 28%, #1e1e1e 55%, var(--pattern-dark) 100%);
  }
  .back-wordmark {
    position: absolute;
    left: 50%; top: 50%;
    transform: translate(-50%, -50%);
    display: flex; align-items: center; gap: 14px;
    color: var(--paper);
    font-weight: 700;
    font-size: 40px;
    letter-spacing: 10px;
  }
  .back-wordmark .mark-dot {
    width: 22px; height: 22px; border-radius: 50%; background: var(--paper);
  }
  /* Front side */
  .card-front { background: var(--paper); }
  .front-shape { position: absolute; inset: 0; }
  .front-wordmark {
    position: absolute;
    left: 34px; top: 120px;
    display: flex; align-items: center; gap: 10px;
    color: var(--ink);
    font-weight: 700;
    font-size: 24px;
    letter-spacing: 5px;
  }
  .front-wordmark .mark-dot {
    width: 14px; height: 14px; border-radius: 50%; background: var(--ink);
  }
  .divider {
    position: absolute;
    left: 228px; top: 52px;
    width: 1.5px; height: 150px;
    background: var(--ink);
  }
  .contact {
    position: absolute;
    left: 248px; top: 52px;
    color: var(--ink);
  }
  .contact-name { font-weight: 700; font-size: 17px; letter-spacing: 0.5px; }
  .contact-title { font-size: 13px; font-weight: 500; margin-top: 2px; }
  .contact-list { list-style: none; margin-top: 16px; font-size: 12.5px; line-height: 1.35; }
  .contact-list li { display: flex; align-items: flex-start; gap: 8px; margin-bottom: 3px; }
  .contact-list svg { flex: none; margin-top: 2px; }
  .tagline { font-family: "Montserrat", Arial, sans-serif; font-size: 12.5px; font-weight: 500; fill: var(--paper); }
</style>
</head>
<body>

  <section class="card card-back">
    <div class="back-pattern" role="img" aria-label="Repeating brand-symbol pattern fading from silver to black"></div>
    <div class="back-wordmark"><span class="mark-dot"></span><span>KELVARA</span></div>
  </section>

  <section class="card card-front">
    <svg class="front-shape" width="560" height="320" viewBox="0 0 560 320">
      <path d="M0,262 Q330,250 560,100 L560,320 L0,320 Z" fill="var(--band)"/>
      <path d="M70,250 Q360,238 545,102" fill="none" stroke="var(--swoosh)" stroke-width="4" stroke-linecap="round"/>
      <path id="tagline-path" d="M150,298 Q370,275 540,150" fill="none"/>
      <text class="tagline"><textPath href="#tagline-path">If it keeps a drink cold or the party going...we do it!</textPath></text>
    </svg>

    <div class="front-wordmark"><span class="mark-dot"></span><span>KELVARA</span></div>
    <div class="divider"></div>

    <div class="contact">
      <div class="contact-name">DALTON PIKES</div>
      <div class="contact-title">Founder and CPO</div>
      <ul class="contact-list">
        <li>
          <svg width="12" height="12" viewBox="0 0 24 24" aria-hidden="true"><path fill="var(--ink)" d="M6.6 10.8a15 15 0 0 0 6.6 6.6l2.2-2.2a1 1 0 0 1 1-.25 11.4 11.4 0 0 0 3.6.57 1 1 0 0 1 1 1V20a1 1 0 0 1-1 1A17 17 0 0 1 3 4a1 1 0 0 1 1-1h3.5a1 1 0 0 1 1 1c0 1.25.2 2.45.57 3.57a1 1 0 0 1-.25 1z"/></svg>
          <span>555.318.4726</span>
        </li>
        <li>
          <svg width="12" height="14" viewBox="0 0 24 28" aria-hidden="true"><path fill="var(--ink)" d="M12 0a9 9 0 0 0-9 9c0 7 9 19 9 19s9-12 9-19a9 9 0 0 0-9-9zm0 13a4 4 0 1 1 0-8 4 4 0 0 1 0 8z"/></svg>
          <span>412 E. Carver Avenue, Ste<br>2207, Tampa, FL. 33917</span>
        </li>
      </ul>
    </div>
  </section>

</body>
</html>
```